refurbishment of diamond cut alloy wheels

we need to design a flyer that will catch the eye of the customer to refurbish diamond cut alloy wheels. we refurbish the wheels by using the latest CNC machine to precision cut and resurface the wheel. we would like before and after pictures of maybe Valtoren, KRT, Pelo wheels to give it a prestige look. The final design should communicate an expensive look and providing a good image for the business. The colours that I would like to use is black and red which should make the flyer stand out. The logo must sit on a black background without the wordings of specialists in GX, Pelo etc and also without servicing, diagnostics etc as well. This flyer is just to communicate refurbishment of alloy wheels to high standard.

Target Market(s)

any members of the public and car dealerships

Industry/Entity Type

Automotive

Colors

Requirements
Must have
• Wow factor with great images of wheels
Nice to have
• Maybe on the front of the flyer it has a picture of a wheel and then on the back of the flyer it has before and after pictures to show how just how incredible it is to refurbish wheels
Should not have
• other makes of wheels apart from KRT, Pelo, and any other high end makes of vehicles wheels

```html
<!DOCTYPE html>
<html lang="en">
<head>
<meta charset="utf-8">
<title>Crestway Motors – Alloy Wheel Refurbishment Flyer</title>
<link rel="stylesheet" href="https://fonts.googleapis.com/css2?family=Oswald:wght@400;500;600&family=Open+Sans:wght@400;600&display=swap">
<style>
:root{
  --red:#d11f26;
  --red-dark:#8e1015;
  --black:#0b0b0c;
  --silver:#c9cbce;
  --white:#ffffff;
  --text:#e6e6e6;
  --stage:#dcdcdc;
}
*{box-sizing:border-box;margin:0;padding:0}
html,body{width:1200px;height:828px;overflow:hidden;background:var(--stage)}
.canvas{position:relative;width:1200px;height:828px}
.flyer{position:absolute;top:52px;width:508px;height:719px;background:var(--black);overflow:hidden;font-family:"Open Sans",sans-serif;color:var(--text)}
.flyer--front{left:71px}
.flyer--back{left:630px}

.title{position:absolute;left:14px;top:22px;white-space:nowrap;font-family:"Oswald",sans-serif;font-weight:500;font-size:24px;letter-spacing:.1px;color:var(--white)}
.photo{position:absolute}
.photo--car{left:0;top:61px;width:508px;height:322px;background:radial-gradient(ellipse at 45% 45%,#b3141c 0%,#5e0b0f 35%,#1d1d20 65%,#0b0b0c 100%)}
.photo--wheels{left:24px;top:87px;width:444px;height:152px;background:radial-gradient(ellipse at 50% 50%,#9a9ca0 0%,#4a4b4f 45%,#121214 100%);border-radius:6px}
.bands{position:absolute;left:0;width:508px}

.badge{position:absolute;width:113px;height:113px}
.badge svg{position:absolute;inset:0}
.badge p{position:absolute;inset:0;display:flex;align-items:center;justify-content:center;text-align:center;font-family:"Oswald",sans-serif;font-size:11.5px;line-height:1.3;color:var(--white)}
.badge--front{left:10px;top:283px}
.badge--back{left:387px;top:265px}

.brand{position:absolute;left:112px;top:388px;width:282px;height:82px;display:flex;align-items:center;justify-content:center;gap:10px;background:linear-gradient(180deg,#2a2a2d,#111);border:2px solid #8a8b8f;border-radius:6px}
.brand__mark{width:20px;height:20px;background:var(--red);flex:none}
.brand__name{white-space:nowrap;font-family:"Oswald",sans-serif;font-weight:600;font-size:28px;color:var(--white);letter-spacing:1px}

.intro{position:absolute;left:16px;top:498px;width:302px;font-size:10.8px;line-height:14.4px}
.intro p+p{margin-top:14px}

.compare{position:absolute;left:346px;width:144px;height:64px;border:2px solid #9a9ca0;border-radius:8px;overflow:hidden}
.compare--before{top:496px;background:radial-gradient(circle at 55% 55%,#b9b2a6,#5b574f 60%,#2a2826)}
.compare--after{top:567px;background:radial-gradient(circle at 55% 55%,#eaeaec,#8d8f94 60%,#303136)}
.compare__tag{position:absolute;left:0;top:6px;background:var(--red);color:var(--white);font-family:"Oswald",sans-serif;font-size:10.5px;padding:1px 12px 1px 6px}

.cta{position:absolute;left:0;width:508px;top:644px;text-align:center;white-space:nowrap;font-family:"Oswald",sans-serif;font-size:12px;letter-spacing:-.1px;color:var(--red)}
.links{position:absolute;left:0;width:508px;top:663px;text-align:center;white-space:nowrap;font-size:11px;color:var(--text)}

.footer{position:absolute;left:0;bottom:0;width:508px;height:34px}
.footer__address{position:absolute;left:0;top:0;height:34px;width:330px;background:var(--red);clip-path:polygon(0 0,100% 0,92% 100%,0 100%);display:flex;align-items:center;gap:6px;padding-left:16px;white-space:nowrap;font-size:11px;color:var(--white)}
.footer__phone{position:absolute;right:14px;top:0;height:34px;display:flex;align-items:center;gap:8px;white-space:nowrap;font-family:"Oswald",sans-serif;font-size:21px;color:var(--white);letter-spacing:.5px}

.services{position:absolute;left:14px;top:409px;width:481px;display:grid;grid-template-columns:1fr 1fr;column-gap:22px;row-gap:12px}
.service{position:relative;height:107px;border:2px solid #55575b;border-radius:8px;background:linear-gradient(90deg,#111 50%,#2b2c30);overflow:hidden;padding:12px 8px}
.service__img{position:absolute;right:0;top:0;width:92px;height:100%}
.service:nth-child(1) .service__img{background:radial-gradient(circle at 60% 50%,#8d8a84,#3a3936 70%)}
.service:nth-child(2) .service__img{background:radial-gradient(circle at 60% 50%,#5a5b60,#1c1c1f 70%)}
.service:nth-child(3) .service__img{background:radial-gradient(circle at 60% 50%,#bdb8ad,#4b4842 70%)}
.service:nth-child(4) .service__img{background:radial-gradient(circle at 60% 50%,#d8d9dc,#55575c 70%)}
.service h3{position:relative;width:128px;font-family:"Oswald",sans-serif;font-weight:400;font-size:10.5px;line-height:1.6;color:var(--white);text-transform:uppercase}
.service p{position:relative;width:126px;margin-top:7px;font-size:7.4px;line-height:1.3;color:var(--text)}
</style>
</head>
<body>
<main class="canvas">

  <section class="flyer flyer--front">
    <h1 class="title">REFURBISHMENT OF DIAMOND CUT ALLOY WHEELS</h1>
    <div class="photo photo--car" role="img" aria-label="Photo of a red sports car with diamond cut alloy wheels in a dark studio"></div>

    <svg class="bands" style="top:330px" width="508" height="150" viewBox="0 0 508 150" aria-hidden="true">
      <polygon points="0,95 508,25 508,45 0,115" fill="#7d7f83"/>
      <polygon points="0,115 508,45 508,62 0,132" fill="#b4161d"/>
      <polygon points="0,132 508,62 508,150 0,150" fill="#0b0b0c"/>
    </svg>

    <div class="badge badge--front">
      <svg viewBox="0 0 113 113" aria-hidden="true">
        <circle cx="56.5" cy="56.5" r="49" fill="none" stroke="#d11f26" stroke-width="10" stroke-dasharray="5 4"/>
        <circle cx="56.5" cy="56.5" r="48" fill="#d11f26"/>
      </svg>
      <p>WE OFFER<br>LOCAL COLLECTION<br>AND DELIVERY</p>
    </div>

    <div class="brand">
      <span class="brand__mark"></span>
      <span class="brand__name">CRESTWAY MOTORS</span>
    </div>

    <div class="intro">
      <p>If you are looking to refresh the look of your car but don’t want the expense of new alloys, with a wide range of limited edition colours to choose from why not consider customising and refurbishing your existing alloys?</p>
      <p>We use the latest technology to refurbish the wheels to a high standard to look like new. We also carry out bodywork using water based paints with our in house paint scheme ensuring a perfect colour match.</p>
    </div>

    <div class="compare compare--before" role="img" aria-label="Alloy wheel before refurbishment"><span class="compare__tag">BEFORE</span></div>
    <div class="compare compare--after" role="img" aria-label="Alloy wheel after refurbishment"><span class="compare__tag">AFTER</span></div>

    <p class="cta">IF YOU NEED PREMIER ALLOY REFURBISHMENT SERVICES IN SLOUGH, PLEASE CONTACT US:</p>
    <p class="links">www.crestwaymotors.co.uk | danny@crestwaymotors.co.uk</p>

    <footer class="footer">
      <div class="footer__address">
        <svg width="10" height="14" viewBox="0 0 10 14" aria-hidden="true"><path d="M5 0C2.2 0 0 2.2 0 5c0 3.6 5 9 5 9s5-5.4 5-9c0-2.8-2.2-5-5-5zm0 7a2 2 0 110-4 2 2 0 010 4z" fill="#fff"/></svg>
        14B Harlow Lane, Fenbridge, Berkshire, SL9 2QT
      </div>
      <div class="footer__phone">
        <svg width="18" height="18" viewBox="0 0 20 20" aria-hidden="true"><circle cx="10" cy="10" r="9" fill="none" stroke="#fff" stroke-width="1.6"/><path d="M7 5.5l1.6 2.4-1 1c.6 1.3 1.6 2.3 2.9 2.9l1-1 2.4 1.6-.9 1.6c-3.4-.3-6.3-3.2-6.6-6.6z" fill="#fff"/></svg>
        01632 960482
      </div>
    </footer>
  </section>

  <section class="flyer flyer--back">
    <div class="photo photo--wheels" role="img" aria-label="Three polished diamond cut alloy wheels side by side"></div>

    <svg class="bands" style="top:255px" width="508" height="160" viewBox="0 0 508 160" aria-hidden="true">
      <polygon points="0,0 254,110 508,0 508,30 254,145 0,30" fill="#8d8f93"/>
      <polygon points="150,70 254,112 358,70 358,80 254,124 150,80" fill="#d11f26"/>
      <polygon points="0,30 254,145 508,30 508,160 0,160" fill="#111113"/>
    </svg>

    <div class="badge badge--back">
      <svg viewBox="0 0 113 113" aria-hidden="true">
        <circle cx="56.5" cy="56.5" r="49" fill="none" stroke="#d11f26" stroke-width="10" stroke-dasharray="5 4"/>
        <circle cx="56.5" cy="56.5" r="48" fill="#d11f26"/>
      </svg>
      <p>WE OFFER<br>LOCAL COLLECTION<br>AND DELIVERY</p>
    </div>

    <div class="services">
      <article class="service">
        <div class="service__img" role="img" aria-label="Worn, corroded alloy wheel"></div>
        <h3>Refurbish old or new<br>alloy wheels to perfection</h3>
        <p>We can also supply replacement split rim outer rims, stainless steel wheel trims, titanium and alloy wheel bolts.</p>
      </article>
      <article class="service">
        <div class="service__img" role="img" aria-label="Dark gloss custom alloy wheel"></div>
        <h3>Pure styling with a<br>touch of class...</h3>
        <p>Using an advanced refurbishment technique, we offer unique color-coding.</p>
      </article>
      <article class="service">
        <div class="service__img" role="img" aria-label="Damaged alloy wheel close-up"></div>
        <h3>We can fix, respray &amp; repair<br>damaged alloy wheels</h3>
        <p>With our advanced technology, alloy wheel bolts, and studs.</p>
      </article>
      <article class="service">
        <div class="service__img" role="img" aria-label="Bright silver refurbished alloy wheel"></div>
        <h3>Fast affordable friendly<br>service</h3>
        <p>We cater to all locations in and around Colnbrook, Windsor, Hayes, Hounslow, Staines, Ascot and Ashford.</p>
      </article>
    </div>

    <p class="cta">IF YOU NEED PREMIER ALLOY REFURBISHMENT SERVICES IN SLOUGH, PLEASE CONTACT US:</p>
    <p class="links">www.crestwaymotors.co.uk | danny@crestwaymotors.co.uk</p>

    <footer class="footer">
      <div class="footer__address">
        <svg width="10" height="14" viewBox="0 0 10 14" aria-hidden="true"><path d="M5 0C2.2 0 0 2.2 0 5c0 3.6 5 9 5 9s5-5.4 5-9c0-2.8-2.2-5-5-5zm0 7a2 2 0 110-4 2 2 0 010 4z" fill="#fff"/></svg>
        14B Harlow Lane, Fenbridge, Berkshire, SL9 2QT
      </div>
      <div class="footer__phone">
        <svg width="18" height="18" viewBox="0 0 20 20" aria-hidden="true"><circle cx="10" cy="10" r="9" fill="none" stroke="#fff" stroke-width="1.6"/><path d="M7 5.5l1.6 2.4-1 1c.6 1.3 1.6 2.3 2.9 2.9l1-1 2.4 1.6-.9 1.6c-3.4-.3-6.3-3.2-6.6-6.6z" fill="#fff"/></svg>
        01632 960482
      </div>
    </footer>
  </section>

</main>
</body>
</html>
```